Letter and Envelope Design For Harborline Realty

Please design a letter and an envelope incorporating our logo (See Attached). We are also launched a business card contest. Since we want them to match, please feel free to submit a design for both the business card and also the letter design and envelope.

Requirements
Must have
• The envelope, the letter and the business cards must match somehow connecting the designs. We want them to have something that holds them together besides the logo.

```html
<!DOCTYPE html>
<html lang="en">
<head>
<meta charset="utf-8">
<title>Harborline Realty – Letterhead and Envelope</title>
<link href="https://fonts.googleapis.com/css2?family=Montserrat:wght@600&family=PT+Sans:wght@400;700&family=Arimo:wght@700&display=swap" rel="stylesheet">
<style>
  :root {
    --brand-blue: #071a8e;
    --swoosh-grey: #6b6b6b;
    --ink: #3a3a3a;
    --ink-soft: #555;
    --paper: #ffffff;
    --stage: #e6e6e6;
    --hairline: #d8d8d8;
    --divider: #9fc3d6;
  }
  * { margin: 0; padding: 0; box-sizing: border-box; }
  html, body { width: 1200px; height: 825px; overflow: hidden; background: var(--stage); }
  .canvas { position: relative; width: 1200px; height: 825px; }

  .sheet { position: absolute; background: var(--paper); border: 1px solid var(--hairline); overflow: hidden; }
  .letter { left: 81px; top: 80px; width: 470px; height: 664px; }
  .envelope-front { left: 575px; top: 248px; width: 541px; height: 235px; }
  .envelope-back { left: 575px; top: 510px; width: 541px; height: 235px; }

  .header-wave { position: absolute; left: 0; top: 0; display: block; }

  .brand { position: absolute; text-align: center; color: var(--brand-blue);
           font-family: "Montserrat", sans-serif; font-weight: 600; }
  .brand-dot { display: block; margin: 0 auto 6px; width: 40px; height: 40px;
               border: 2px solid var(--brand-blue); border-radius: 50%; }
  .brand-name { display: block; font-size: 11.5px; letter-spacing: 1.4px; line-height: 1.2; }
  .brand-sub { display: block; font-size: 7px; letter-spacing: 3px; line-height: 1.4; }
  .letter .brand { left: 37px; top: 26px; width: 104px; }
  .envelope-front .brand { left: 30px; top: 26px; width: 104px; }

  .salutation { position: absolute; left: 41px; top: 128px; font-family: "Arimo", sans-serif;
                font-weight: 700; font-size: 10.5px; color: var(--ink); }
  .letter-body { position: absolute; left: 41px; top: 154px; width: 393px;
                 font-family: "PT Sans", sans-serif; font-size: 9.3px; line-height: 12.3px; color: var(--ink-soft); }
  .letter-body p { text-align: justify; margin-bottom: 12.3px; }

  .signature { position: absolute; left: 37px; top: 503px; width: 89px; height: 43px;
               background: linear-gradient(135deg, #f1f1f1, #dcdcdc); border-radius: 4px; }

  .letter-footer { position: absolute; left: 0; top: 612px; width: 100%; height: 44px;
                   font-family: "PT Sans", sans-serif; font-size: 7.4px; line-height: 12px; color: var(--ink-soft); }
  .footer-col { position: absolute; top: 0; width: 140px; margin-left: -70px; text-align: center; }
  .footer-col svg { display: block; margin: 0 auto 4px; }
  .footer-col b { color: var(--ink); }
  .col-address { left: 98px; }
  .col-phone { left: 240px; }
  .col-web { left: 412px; }
  .footer-divider { position: absolute; top: 2px; width: 1px; height: 40px; background: var(--divider); }
  .footer-divider.first { left: 172px; }
  .footer-divider.second { left: 310px; }
  .letter-baseband { position: absolute; left: 0; bottom: 0; width: 100%; height: 4px; background: var(--brand-blue); }

  .return-address { position: absolute; left: 32px; top: 100px; font-family: "PT Sans", sans-serif;
                    font-size: 6.8px; line-height: 9px; color: var(--ink); padding-left: 10px; }
  .return-address svg { position: absolute; left: 0; top: 1px; }
  .address-window { position: absolute; left: 31px; top: 137px; width: 209px; height: 62px;
                    border: 1px solid #e2e2e2; border-radius: 5px; }
  .address-line { position: absolute; left: 8px; right: 8px; border-top: 1px dotted #b9b9b9; }

  .flap { position: absolute; left: 0; top: 0; display: block; }
  .flap-brand { position: absolute; left: 0; top: 28px; width: 100%; text-align: center;
                font-family: "Montserrat", sans-serif; font-weight: 600; font-size: 8.5px;
                letter-spacing: 1.4px; color: var(--brand-blue); }
  .envelope-web { position: absolute; left: 0; top: 217px; width: 100%; text-align: center;
                  font-family: "PT Sans", sans-serif; font-size: 6.8px; color: var(--brand-blue); }
  .envelope-web::before, .envelope-web::after { content: ""; display: inline-block; width: 18px;
                  height: 1px; background: var(--brand-blue); vertical-align: middle; margin: 0 3px; }
</style>
</head>
<body>
<div class="canvas">

  <section class="sheet letter" aria-label="Letterhead">
    <svg class="header-wave" width="470" height="40" viewBox="0 0 470 40" aria-hidden="true">
      <path d="M0 0 H470 V37 C320 16 140 9 0 12 Z" fill="var(--brand-blue)"/>
      <path d="M0 14 C160 8 330 15 470 38 C330 20 160 16 0 21 Z" fill="var(--swoosh-grey)"/>
    </svg>
    <div class="brand">
      <span class="brand-dot"></span>
      <span class="brand-name">HARBORLINE</span>
      <span class="brand-sub">REALTY</span>
    </div>

    <p class="salutation">Dear Mr. Ellis,</p>
    <div class="letter-body">
      <p>Lorem Ipsum is simply dummy text of the printing and typesetting industry. Lorem Ipsum has been the industry's standard dummy text ever since the 1500s, when an unknown printer took a galley of type and scrambled it to make a type specimen book. It has survived not only five centuries, but also the leap into electronic typesetting, remaining essentially unchanged.</p>
      <p>The standard chunk of Lorem Ipsum used since the 1500s is reproduced below for those interested. Sections 1.10.32 and 1.10.33 from "de Finibus Bonorum et Malorum" by Aurelian are also reproduced in their exact original form, accompanied by English versions from the 1914 translation by L. Hartwell</p>
      <p>Lorem Ipsum is simply dummy text of the printing and typesetting industry. Lorem Ipsum has been the industry's standard dummy text ever since the 1500s, when an unknown printer took a galley of type and scrambled it to make a type specimen book. It has survived not only five centuries, but also the leap into electronic typesetting, remaining essentially unchanged. It was popularised in the</p>
      <p>Lorem Ipsum is simply dummy text of the printing and typesetting industry. Lorem Ipsum has been the industry's standard dummy text ever since the 1500s, when an unknown printer took a galley of type and scrambled it to make a type specimen book. It has survived not only five centuries, but also the leap into electronic typesetting, remaining essentially unchanged. It was popularised in the</p>
      <p>Lorem Ipsum is simply dummy text of the printing and typesetting industry. Lorem Ipsum has been the industry's standard dummy text ever since the 1500s, when an unknown printer took a galley of type and scrambled it to make a type specimen book.</p>
    </div>

    <div class="signature" role="img" aria-label="Handwritten signature of the sender"></div>

    <footer class="letter-footer">
      <div class="footer-col col-address">
        <svg width="9" height="11" viewBox="0 0 9 11" aria-hidden="true"><path d="M4.5 10.5 C1.5 6.5 0.8 5 0.8 4 A3.7 3.7 0 0 1 8.2 4 C8.2 5 7.5 6.5 4.5 10.5 Z" fill="none" stroke="var(--brand-blue)" stroke-width="1.1"/><circle cx="4.5" cy="4" r="1.3" fill="var(--brand-blue)"/></svg>
        Po. box 201, Street Name,<br>City Name, Zip Code - 00000
      </div>
      <span class="footer-divider first"></span>
      <div class="footer-col col-phone">
        <svg width="11" height="11" viewBox="0 0 11 11" aria-hidden="true"><circle cx="5.5" cy="5.5" r="4.9" fill="none" stroke="var(--brand-blue)" stroke-width="0.9"/><path d="M6.6 2.8 C4.2 3.2 3.4 6.6 4.6 8.2 L5.5 7.4 C5 6.6 5.2 5 6 4.4 Z" fill="var(--brand-blue)"/></svg>
        <b>P:</b> (555) 014-0012<br><b>F:</b> (555) 014-0012
      </div>
      <span class="footer-divider second"></span>
      <div class="footer-col col-web">
        <svg width="11" height="11" viewBox="0 0 11 11" aria-hidden="true" fill="none" stroke="var(--brand-blue)" stroke-width="0.8"><circle cx="5.5" cy="5.5" r="4.8"/><ellipse cx="5.5" cy="5.5" rx="2" ry="4.8"/><path d="M0.7 5.5 H10.3 M1.5 3 H9.5 M1.5 8 H9.5"/></svg>
        info@harborlinerealty.com<br>www.harborlinerealty.com
      </div>
    </footer>
    <span class="letter-baseband"></span>
  </section>

  <section class="sheet envelope-front" aria-label="Envelope front">
    <svg class="header-wave" width="541" height="44" viewBox="0 0 541 44" aria-hidden="true">
      <path d="M0 0 H541 V41 C370 20 160 10 0 10 Z" fill="var(--brand-blue)"/>
      <path d="M0 13 C180 7 380 16 541 42 C380 22 180 17 0 21 Z" fill="var(--swoosh-grey)"/>
    </svg>
    <div class="brand">
      <span class="brand-dot"></span>
      <span class="brand-name">HARBORLINE</span>
      <span class="brand-sub">REALTY</span>
    </div>
    <div class="return-address">
      <svg width="7" height="9" viewBox="0 0 7 9" aria-hidden="true"><path d="M3.5 9 C1 5.5 0 4.3 0 3.3 A3.5 3.5 0 0 1 7 3.3 C7 4.3 6 5.5 3.5 9 Z" fill="var(--brand-blue)"/><circle cx="3.5" cy="3.3" r="1.2" fill="#fff"/></svg>
      Po. box 201, Street Name,<br>City Name, Zip Code - 00000
    </div>
    <div class="address-window" aria-label="Recipient address area">
      <span class="address-line" style="top:17px"></span>
      <span class="address-line" style="top:29px"></span>
      <span class="address-line" style="top:41px"></span>
      <span class="address-line" style="top:53px"></span>
    </div>
  </section>

  <section class="sheet envelope-back" aria-label="Envelope back">
    <svg class="flap" width="541" height="80" viewBox="0 0 541 80" aria-hidden="true">
      <path d="M2 0 C6 20 12 30 32 35 L240 62 Q270 70 300 62 L509 35 C529 30 535 20 539 0" fill="none" stroke="#e4e4e4" stroke-width="2"/>
    </svg>
    <div class="flap-brand">HARBORLINE REALTY</div>
    <div class="envelope-web">www.harborlinerealty.com</div>
  </section>

</div>
</body>
</html>
```